Kestrel Facilities Business Card Design

We would now like to design business cards with the new Kestrel Facilities logo

Target Market(s)

Professional

Industry/Entity Type

Professional services

Contact Information for Business Card

Employee name, title, phone number, email address, corporate office address and logo.

Font styles to use
Sans Serif

Colors
0054AA
0677BA
7BADD7
CADEEF
E8F1F8

Requirements
Must have
• My logo
Should not have
• any other pictures or images besides my logo

```html
<!DOCTYPE html>
<html lang="en">
<head>
<meta charset="utf-8">
<title>Kestrel Facilities – Business Card</title>
<link rel="stylesheet" href="https://fonts.googleapis.com/css2?family=Oswald:wght@500&family=Lato:wght@400&display=swap">
<style>
  :root {
    --stage: #1b1b1b;
    --card: #111111;
    --brand-blue: #0a7fe6;
    --text-light: #f2f2f2;
    --divider: #6a6a6a;
  }
  * { margin: 0; padding: 0; box-sizing: border-box; }
  html, body {
    width: 1200px; height: 900px; overflow: hidden;
    background: var(--stage);
  }
  .stage {
    position: relative; width: 1200px; height: 900px;
    display: flex; flex-direction: column; align-items: center; justify-content: center; gap: 48px;
  }
  .card {
    position: relative; width: 560px; height: 320px;
    background: var(--card);
    box-shadow: 0 10px 30px rgba(0,0,0,0.6);
    overflow: hidden;
  }
  .card__band {
    position: absolute; left: 0; right: 0; bottom: 0; height: 9px;
    background: var(--brand-blue);
  }
  /* Front */
  .card--front { display: flex; align-items: center; justify-content: center; }
  .brand {
    display: flex; align-items: center; gap: 16px; margin-bottom: 10px;
  }
  .brand__square {
    width: 54px; height: 54px; background: var(--brand-blue);
  }
  .brand__name {
    font-family: "Oswald", sans-serif; font-weight: 500;
    font-size: 44px; letter-spacing: 2px; text-transform: uppercase;
    color: var(--brand-blue); line-height: 1;
  }
  /* Back */
  .person {
    position: absolute; left: 48px; top: 112px; width: 210px; text-align: right;
  }
  .person__name {
    font-family: "Oswald", sans-serif; font-weight: 500;
    font-size: 30px; text-transform: uppercase; color: var(--brand-blue);
    line-height: 1.05; letter-spacing: -0.3px;
  }
  .person__title {
    font-family: "Lato", sans-serif; font-size: 15px; color: var(--text-light);
    margin-top: 2px;
  }
  .divider {
    position: absolute; left: 284px; top: 116px; width: 1px; height: 84px;
    background: var(--divider);
  }
  .contacts {
    position: absolute; left: 306px; top: 120px; list-style: none;
    font-family: "Lato", sans-serif; font-size: 15px; color: var(--text-light);
  }
  .contacts__item { display: flex; align-items: center; gap: 9px; height: 26px; }
  .contacts__icon { width: 15px; height: 15px; flex: none; }
  .address {
    position: absolute; left: 48px; right: 48px; bottom: 34px; text-align: center;
    font-family: "Lato", sans-serif; font-size: 15px; color: var(--text-light);
  }
</style>
</head>
<body>
<main class="stage">
  <section class="card card--front" aria-label="Card front">
    <div class="brand">
      <span class="brand__square"></span>
      <span class="brand__name">Kestrel Facilities</span>
    </div>
    <div class="card__band"></div>
  </section>

  <section class="card card--back" aria-label="Card back">
    <div class="person">
      <p class="person__name">Daniel Reyes</p>
      <p class="person__title">Managing Director</p>
    </div>
    <div class="divider"></div>
    <ul class="contacts">
      <li class="contacts__item">
        <svg class="contacts__icon" viewBox="0 0 16 16" aria-hidden="true"><path fill="#0a7fe6" d="M3.6 1.2l2.2 2.6-1.3 1.8c.9 2 2.3 3.5 4.6 4.7l1.7-1.3 2.7 2.2-1.2 2.3C7.2 15 1 8.8 1.5 2.4z"/></svg>
        <span>044-987 654 321</span>
      </li>
      <li class="contacts__item">
        <svg class="contacts__icon" viewBox="0 0 16 16" aria-hidden="true"><rect x="1" y="3" width="14" height="10" fill="#0a7fe6"/><path d="M1.5 3.5L8 9l6.5-5.5" fill="none" stroke="#111" stroke-width="1.3"/></svg>
        <span>hello@kestrelfm.com</span>
      </li>
      <li class="contacts__item">
        <svg class="contacts__icon" viewBox="0 0 16 16" aria-hidden="true"><g fill="none" stroke="#0a7fe6" stroke-width="1.4"><circle cx="8" cy="8" r="6.5"/><ellipse cx="8" cy="8" rx="3" ry="6.5"/><path d="M1.5 8h13M2.5 4.8h11M2.5 11.2h11"/></g></svg>
        <span>www.kestrelfm.com</span>
      </li>
    </ul>
    <p class="address">58, Harbour Road, Westvale, 30917</p>
    <div class="card__band"></div>
  </section>
</main>
</body>
</html>
```